Business card for Luxury Portable Restroom Trailer company

We are a Luxury Portable Restroom Trailer Company Called FALCRIDGE HIRES. Based in Orange County California. We provide portable restroom trailers for events, such as, Weddings, Concerts, Charity events, Sporting events, Tournaments, Corporate events, ect. We rent and Sell the Luxury restrooms. Our colors are white, grey, and Orange. As you will see in the logo we uploaded.
There are 2 people in the company so the names and titles will change for the 3 people but card will remain the same. Here is the information for each Person: Dwight Penner CFO 555 318-0476
next Person: Leon Marchetti VP 555 318-0476
Next Person: Owen Marchetti CEO 555 318-0476
Information to include on the card: Luxury Restroom Trailers Rental and Sales. Weddings, Concerts, Charity, Sporting and Corp. Events.

```html
<!DOCTYPE html>
<html lang="en">
<head>
<meta charset="utf-8">
<title>Falcridge Hires – Business Card</title>
<link href="https://fonts.googleapis.com/css2?family=Montserrat:wght@400;500;700;800&display=swap" rel="stylesheet">
<style>
  :root {
    --page-bg: #1c1c1d;
    --card-white: #ffffff;
    --card-dark: #2c2c2e;
    --pattern-light: #3a3a3c;
    --pattern-dark: #262628;
    --band-grey: #565658;
    --brand-orange: #f26a1b;
    --text-grey: #4a4a4c;
    --text-white: #ffffff;
  }
  * { box-sizing: border-box; margin: 0; padding: 0; }
  html, body {
    width: 1200px; height: 900px; overflow: hidden;
    background: var(--page-bg);
    font-family: 'Montserrat', sans-serif;
  }
  .stage {
    width: 1200px; height: 900px;
    display: flex; flex-direction: column;
    align-items: center; justify-content: center;
    gap: 60px;
  }
  .card {
    position: relative;
    width: 640px; height: 366px;
    border-radius: 20px;
    overflow: hidden;
    box-shadow: 0 18px 40px rgba(0,0,0,0.55);
  }

  /* Front */
  .card--front { background: var(--card-white); }
  .card__rule {
    position: absolute; left: 0; top: 242px;
    width: 100%; height: 4px;
    background: var(--brand-orange);
  }
  .card__band {
    position: absolute; left: 0; top: 246px;
    width: 100%; height: 120px;
    background: var(--band-grey);
    padding: 28px 40px 0;
  }
  .brand {
    position: absolute; left: 40px; top: 108px;
    display: flex; align-items: center; gap: 10px;
    white-space: nowrap;
  }
  .brand__mark {
    width: 16px; height: 16px; flex: none;
    background: var(--brand-orange);
  }
  .brand__name {
    font-weight: 800;
    font-size: 24px;
    line-height: 1;
    letter-spacing: 0.5px;
    color: var(--brand-orange);
  }
  .divider {
    position: absolute; left: 326px; top: 50px;
    width: 2px; height: 178px;
    background: var(--brand-orange);
  }
  .contact {
    position: absolute; left: 350px; top: 62px;
    right: 16px;
  }
  .contact__name {
    font-weight: 800;
    font-size: 22px;
    letter-spacing: 1px;
    text-transform: uppercase;
    color: var(--brand-orange);
    line-height: 1;
    white-space: nowrap;
  }
  .contact__title {
    font-weight: 400;
    font-size: 16px;
    color: var(--text-grey);
    margin-top: 5px;
    letter-spacing: 1px;
  }
  .contact__list { list-style: none; margin-top: 18px; }
  .contact__item {
    display: flex; align-items: center; gap: 9px;
    font-size: 14px;
    color: var(--text-grey);
    line-height: 1;
    margin-bottom: 10px;
    white-space: nowrap;
  }
  .contact__icon { width: 12px; height: 12px; flex: none; }
  .tagline {
    font-weight: 500;
    font-size: 18px;
    color: var(--brand-orange);
    letter-spacing: 0.3px;
    white-space: nowrap;
  }
  .events {
    font-weight: 400;
    font-size: 18px;
    color: var(--text-white);
    margin-top: 10px;
    letter-spacing: 0.3px;
    white-space: nowrap;
  }

  /* Back */
  .card--back { background: var(--card-dark); }
  .back__pattern {
    position: absolute; inset: 0;
    background: linear-gradient(135deg, var(--pattern-dark) 0%, var(--pattern-light) 55%, var(--pattern-dark) 100%);
  }
  .back__brand {
    position: absolute; left: 40px; bottom: 36px;
    display: flex; align-items: center; gap: 12px;
    white-space: nowrap;
  }
  .back__mark {
    width: 34px; height: 34px; flex: none;
    border: 4px solid var(--brand-orange);
    border-radius: 50%;
  }
  .back__name {
    font-weight: 800;
    font-size: 18px;
    letter-spacing: 0.5px;
    color: var(--brand-orange);
  }
</style>
</head>
<body>
<main class="stage">
  <article class="card card--front">
    <div class="brand">
      <span class="brand__mark"></span>
      <span class="brand__name">FALCRIDGE HIRES</span>
    </div>
    <div class="divider"></div>
    <div class="contact">
      <h1 class="contact__name">Owen Marchetti</h1>
      <p class="contact__title">CEO</p>
      <ul class="contact__list">
        <li class="contact__item">
          <svg class="contact__icon" viewBox="0 0 16 16" aria-hidden="true">
            <path fill="#f26a1b" d="M3.6 1.2l2.3 2.9-1.3 1.6c.9 2 2.6 3.7 4.6 4.6l1.6-1.3 2.9 2.3-1.4 2.2C7 13.2 2.8 9 1.4 3.2z"/>
          </svg>
          555 318-0476
        </li>
        <li class="contact__item">
          <svg class="contact__icon" viewBox="0 0 16 16" aria-hidden="true">
            <rect x="1" y="3" width="14" height="10" rx="1" fill="#f26a1b"/>
            <path d="M1.5 3.8L8 9l6.5-5.2" fill="none" stroke="#fff" stroke-width="1.3"/>
          </svg>
          owen@falcridgehires.com
        </li>
        <li class="contact__item">
          <svg class="contact__icon" viewBox="0 0 16 16" aria-hidden="true">
            <circle cx="8" cy="8" r="7" fill="#f26a1b"/>
            <ellipse cx="8" cy="8" rx="3" ry="7" fill="none" stroke="#fff" stroke-width="1"/>
            <path d="M1 8h14" stroke="#fff" stroke-width="1"/>
          </svg>
          www.falcridgehires.com
        </li>
      </ul>
    </div>
    <div class="card__rule"></div>
    <section class="card__band">
      <p class="tagline">Luxury Restroom Trailers Rental and Sales</p>
      <p class="events">Weddings / Concerts / Charity / Sporting / Corp</p>
    </section>
  </article>

  <article class="card card--back">
    <div class="back__pattern" role="img" aria-label="Repeating tone-on-tone brand pattern in dark greys covering the card back"></div>
    <div class="back__brand">
      <span class="back__mark"></span>
      <span class="back__name">FALCRIDGE HIRES</span>
    </div>
  </article>
</main>
</body>
</html>
```